Consulting company business cards

We have a base design, but would be willing to update. We have a new logo/"tag" that needs to be added. Current business card design is attached for reference into our "style."

Industry/Entity Type

Business

Contact Information for Business Card

Should contain name and title, office number, mobile number if appropriate, e-mail, website, physical address, and company logo.

Font styles to use
Other font styles liked:
• See current card design on KorvandBCard

Colors
0455a3
85acd3
aaaaaa

Requirements
Must have
• Our colors are navy blue, gray, and a lighter blue
Nice to have
• Design that I can easily drop in new names/titles as we hire employees.

```html
<!DOCTYPE html>
<html lang="en">
<head>
<meta charset="utf-8">
<title>Tessler Business Cards</title>
<link rel="stylesheet" href="https://fonts.googleapis.com/css2?family=Lato:wght@400;700&family=Oswald:wght@600&display=swap">
<style>
  :root {
    --stage: #1c1c1e;
    --navy: #0f3b5e;
    --navy-deep: #0b2f4c;
    --paper: #f4f6f8;
    --light-blue: #85acd3;
    --grey: #aaaaaa;
    --white: #ffffff;
  }
  * { margin: 0; padding: 0; box-sizing: border-box; }
  html, body { width: 1200px; height: 873px; overflow: hidden; background: var(--stage); }
  .canvas { position: relative; width: 1200px; height: 873px; }

  .card {
    position: absolute;
    width: 540px; height: 309px;
    border-radius: 16px;
    background: var(--navy);
    overflow: hidden;
    font-family: "Lato", sans-serif;
    color: var(--white);
  }

  /* Back of card */
  .card-back { left: 60px; top: 80px; }
  .brand-strip {
    position: absolute; right: 0; top: 0; bottom: 0; width: 130px;
    background: var(--paper);
    display: flex; align-items: center; justify-content: center; gap: 10px;
  }
  .brand-rules {
    position: absolute; right: 130px; top: 0; bottom: 0; width: 22px;
    border-left: 4px solid var(--paper);
    border-right: 4px solid var(--paper);
  }
  .brand-rules::after {
    content: ""; position: absolute; left: 5px; top: 0; bottom: 0; width: 4px; background: var(--paper);
  }
  .brand-name {
    writing-mode: vertical-rl;
    font-family: "Oswald", sans-serif; font-weight: 600;
    font-size: 46px; letter-spacing: 3px; color: var(--navy);
    line-height: 1;
  }
  .brand-tagline {
    writing-mode: vertical-rl;
    font-size: 11px; letter-spacing: 2.5px; text-transform: uppercase; color: var(--navy);
  }
  .person { position: absolute; left: 36px; top: 38px; }
  .person-name { font-size: 19px; color: var(--grey); }
  .person-name strong { color: var(--white); font-weight: 700; }
  .person-title { font-size: 11px; font-style: italic; color: var(--grey); margin-top: 3px; }
  .address { position: absolute; left: 36px; top: 128px; font-size: 14px; font-weight: 700; }
  .contacts { position: absolute; left: 36px; top: 196px; list-style: none; }
  .contacts li { display: flex; align-items: center; gap: 10px; font-size: 14px; font-weight: 700; margin-bottom: 7px; }
  .contacts svg { width: 16px; height: 14px; fill: var(--white); }

  /* Front of card */
  .card-front { left: 600px; top: 484px; }
  .mark-disc {
    position: absolute; right: 46px; top: 44px;
    width: 140px; height: 140px; border-radius: 50%; background: var(--paper);
  }
  .front-name {
    position: absolute; left: 36px; bottom: 70px;
    font-family: "Oswald", sans-serif; font-weight: 600;
    font-size: 76px; letter-spacing: 4px; line-height: 1; color: var(--paper);
  }
  .front-url {
    position: absolute; left: 38px; bottom: 34px;
    font-size: 16px; font-weight: 700; letter-spacing: 6px; color: var(--paper);
  }
</style>
</head>
<body>
<div class="canvas">

  <section class="card card-back" aria-label="Business card back">
    <div class="person">
      <p class="person-name">Dana <strong>Korvand</strong></p>
      <p class="person-title">Office Manager</p>
    </div>
    <p class="address">1850 N Harbor Ave Westfield Ohio 45011</p>
    <ul class="contacts">
      <li>
        <svg viewBox="0 0 16 14" aria-hidden="true"><path d="M1 4c0-2 3-3 7-3s7 1 7 3v1h-4V4H5v1H1zM3 6h10l2 7H1z"/></svg>
        555.214.3308
      </li>
      <li>
        <svg viewBox="0 0 16 14" aria-hidden="true"><path d="M4 1h8v3H4zM1 5h14v6h-3v2H4v-2H1zM5 9v3h6V9z"/></svg>
        555.214.3342
      </li>
      <li>
        <svg viewBox="0 0 16 14" aria-hidden="true"><path d="M1 2h14v10H1zM2 3l6 5 6-5" stroke="#0f3b5e" stroke-width="1.2"/></svg>
        Dkorvand@Tesslertech.com
      </li>
    </ul>
    <div class="brand-rules"></div>
    <div class="brand-strip">
      <span class="brand-tagline">A Cloud Consulting Company</span>
      <span class="brand-name">TESSLER</span>
    </div>
  </section>

  <section class="card card-front" aria-label="Business card front">
    <div class="mark-disc"></div>
    <p class="front-name">TESSLER</p>
    <p class="front-url">www.Tesslertech.com</p>
  </section>

</div>
</body>
</html>
```